Corvane Freight Company Business Card Design

We are a company that delivers natural saltwater (from the ocean) to aquarium companies, restaurants and home marine tanks. I would like a new business card to suit.

Must include Name, company name, abn, contact number and website as well as logo (see attached).

Looking for a design that stands out, has a clean but unique appearance.

Double and single sided entries welcome

Business

• Logo

```html
<!DOCTYPE html>
<html lang="en">
<head>
<meta charset="utf-8">
<title>Corvane Freight Company – Business Card</title>
<link href="https://fonts.googleapis.com/css2?family=Source+Sans+3:wght@400;600;700&display=swap" rel="stylesheet">
<style>
  :root {
    --backdrop: #2e2420;
    --card-white: #ffffff;
    --brand-blue: #005baa;
    --accent-blue: #1f73c4;
    --sky-blue: #2a9ad8;
    --rule-grey: #b5b5b5;
  }
  * { margin: 0; padding: 0; box-sizing: border-box; }
  html, body {
    width: 1200px; height: 471px; overflow: hidden;
    background: var(--backdrop);
    font-family: "Source Sans 3", Arial, sans-serif;
  }
  .canvas { position: relative; width: 1200px; height: 471px; }

  .card-front {
    position: absolute; left: 50px; top: 86px; width: 520px; height: 296px;
    background: var(--card-white); border-radius: 20px; overflow: hidden;
  }
  .edge-tab {
    position: absolute; top: 124px; width: 14px; height: 60px;
    background: var(--accent-blue);
  }
  .edge-tab--left { left: 0; border-right: 3px solid var(--card-white); box-shadow: inset -2px 0 0 var(--accent-blue); }
  .edge-tab--right { right: 0; }

  .brand-block {
    position: absolute; left: 30px; top: 112px; width: 260px; text-align: center;
  }
  .brand-name {
    color: var(--sky-blue); font-size: 30px; font-weight: 600; line-height: 1.02;
  }
  .abn {
    margin-top: 10px; color: var(--accent-blue); font-size: 13px; letter-spacing: .3px;
  }

  .divider {
    position: absolute; left: 307px; top: 58px; width: 2px; height: 180px;
    background: linear-gradient(to bottom, transparent, var(--rule-grey) 20%, var(--rule-grey) 80%, transparent);
  }

  .contact {
    position: absolute; left: 337px; top: 74px; color: var(--accent-blue);
  }
  .contact-name { font-size: 18px; font-weight: 700; line-height: 1.1; }
  .contact-title { font-size: 14px; margin-top: 2px; }
  .contact-list { list-style: none; margin-top: 18px; font-size: 13px; }
  .contact-list li { display: flex; align-items: center; gap: 6px; height: 20px; }
  .contact-list svg { width: 10px; height: 10px; fill: none; stroke: var(--accent-blue); stroke-width: 1.4; }
  .address { margin-top: 14px; font-size: 13px; line-height: 18px; }

  .card-back {
    position: absolute; left: 619px; top: 84px; width: 525px; height: 299px;
    background: var(--brand-blue); border-radius: 22px;
    border: 1px solid #7fa6cf;
    display: flex; align-items: center; justify-content: center;
  }
  .back-name {
    color: var(--card-white); font-size: 54px; font-weight: 600; line-height: 1.0;
    text-align: center;
  }
</style>
</head>
<body>
<main class="canvas">
  <section class="card-front" aria-label="Card front">
    <span class="edge-tab edge-tab--left"></span>
    <span class="edge-tab edge-tab--right"></span>

    <div class="brand-block">
      <div class="brand-name">Corvane Freight<br>Company</div>
      <p class="abn">ABN: 123456789</p>
    </div>

    <span class="divider"></span>

    <div class="contact">
      <p class="contact-name">Your Name</p>
      <p class="contact-title">Title</p>
      <ul class="contact-list">
        <li>
          <svg viewBox="0 0 10 10" aria-hidden="true"><path d="M2 1 L3.6 1 L4.2 3 L3.2 3.8 Q4.2 5.8 6.2 6.8 L7 5.8 L9 6.4 L9 8 Q8.6 9 7.5 9 Q1 8 1 2.5 Q1 1 2 1 Z"/></svg>
          123-456-7892
        </li>
        <li>
          <svg viewBox="0 0 10 10" aria-hidden="true"><circle cx="5" cy="5" r="4"/><ellipse cx="5" cy="5" rx="1.8" ry="4"/><path d="M1 5 H9"/></svg>
          www.corvanefreight.com
        </li>
      </ul>
      <p class="address">Street Name, City Name<br>State, Zip Code</p>
    </div>
  </section>

  <section class="card-back" aria-label="Card back">
    <div class="back-name">Corvane Freight<br>Company</div>
  </section>
</main>
</body>
</html>
```